MRT Property - Business Cards

Looking for a business card & general letterhead, signage etc design for our new logo.

Colours:
000a20
0056a2
00b5ef
0088ce
68cef2

Fonts:
Poppins
Karla

Please keep look and feel of new brand - example in the zip package I sent.

```html
<!DOCTYPE html>
<html lang="en">
<head>
<meta charset="utf-8">
<title>MRT Property – Letterhead</title>
<link href="https://fonts.googleapis.com/css2?family=Poppins:wght@400;600&display=swap" rel="stylesheet">
<style>
  :root {
    --ink: #000a20;
    --navy: #0056a2;
    --sky: #00b5ef;
    --blue: #0088ce;
    --ice: #68cef2;
    --paper: #ffffff;
    --backdrop: #929196;
  }
  * { margin: 0; padding: 0; box-sizing: border-box; }
  html, body {
    width: 1200px;
    height: 792px;
    overflow: hidden;
    background: var(--backdrop);
    font-family: "Poppins", sans-serif;
  }
  .canvas {
    position: relative;
    width: 1200px;
    height: 792px;
  }
  .letterhead {
    position: absolute;
    left: 338px;
    top: 26px;
    width: 523px;
    height: 739px;
    background: var(--paper);
    overflow: hidden;
  }
  .brand {
    position: absolute;
    top: 42px;
    left: 0;
    width: 100%;
    display: flex;
    justify-content: center;
    align-items: center;
    gap: 10px;
  }
  .brand-dot {
    width: 22px;
    height: 22px;
    border-radius: 50%;
    background: var(--sky);
  }
  .brand-name {
    font-family: "Poppins", sans-serif;
    font-weight: 600;
    font-size: 30px;
    line-height: 1;
    color: var(--navy);
    letter-spacing: 0.5px;
  }
  .contact {
    position: absolute;
    font-size: 10.5px;
    color: var(--ink);
    display: flex;
    align-items: center;
    gap: 4px;
    white-space: nowrap;
  }
  .contact svg { width: 9px; height: 9px; flex: none; }
  .contact-address { top: 665px; left: 0; width: 100%; justify-content: center; }
  .contact-phone { top: 689px; left: 22px; }
  .contact-email { top: 688px; left: 180px; }
  .contact-web { top: 688px; left: 355px; }
  .rule-light {
    position: absolute;
    left: 0;
    top: 709px;
    width: 100%;
    height: 2px;
    background: var(--ice);
  }
  .band {
    position: absolute;
    left: 0;
    bottom: 0;
    width: 100%;
    height: 24px;
    background: var(--blue);
  }
</style>
</head>
<body>
<main class="canvas">
  <section class="letterhead">
    <header class="brand">
      <span class="brand-dot"></span>
      <span class="brand-name">MRT Property</span>
    </header>

    <p class="contact contact-address">
      <svg viewBox="0 0 10 10" aria-hidden="true"><path d="M5 0.5a3 3 0 0 1 3 3c0 2.2-3 5.5-3 5.5S2 5.7 2 3.5a3 3 0 0 1 3-3z" fill="none" stroke="var(--blue)" stroke-width="1.2"/><circle cx="5" cy="3.5" r="1" fill="var(--blue)"/></svg>
      Suite 4.12, Level 4, 18 Harbour Lane, Riverside NSW 2150
    </p>

    <p class="contact contact-phone">
      <svg viewBox="0 0 10 10" aria-hidden="true"><path d="M2.2 0.8l1.6 1.8-0.9 1.2c0.6 1.3 1.6 2.3 2.9 2.9l1.2-0.9 1.8 1.6-1 1.4C4.6 8.6 1.4 5.4 0.8 2z" fill="var(--blue)"/></svg>
      +61 2 5550 0142
    </p>
    <p class="contact contact-email">
      <svg viewBox="0 0 10 10" aria-hidden="true"><rect x="0.8" y="2" width="8.4" height="6" fill="none" stroke="var(--blue)" stroke-width="1.1"/><path d="M0.8 2l4.2 3.4L9.2 2" fill="none" stroke="var(--blue)" stroke-width="1.1"/></svg>
      info@mrtproperty.com.au
    </p>
    <p class="contact contact-web">
      <svg viewBox="0 0 10 10" aria-hidden="true"><circle cx="5" cy="5" r="4.2" fill="none" stroke="var(--blue)" stroke-width="1.1"/><path d="M0.8 5h8.4M5 0.8c-2.4 2.4-2.4 6 0 8.4M5 0.8c2.4 2.4 2.4 6 0 8.4" fill="none" stroke="var(--blue)" stroke-width="0.8"/></svg>
      www.mrtproperty.com.au
    </p>

    <div class="rule-light"></div>
    <div class="band"></div>
  </section>
</main>
</body>
</html>
```